Tellmora Corporate Stationery

Look for design of all new corporate stationery for an existing insurance broking business that is going through a redesign and move from older partners to younger family members. New Logo is attached. Company is Brisbane based.
Colours in the Logo is Hex #43bed8 and website features a lot of hex #17b8d8. Website front page "A plan to protect you" - headline. "Professional and Individual advice to protect your greatest assets" - tagline.

Stationery required: Business Cards, Letter head, Thank-you cards, Birthday cards, Presentation folders, With Compliment slips and a powerpoint template. We also would like to send a card to all customers with the something along of the lines of "something new".

Target Market(s)

Customers of Insurance business looking at superannuation, life and income protection insurance, investment advice and wills

Industry/Entity Type

Insurance Broker

Font styles to use
Other font styles liked:
• same as logo

Requirements
Must have
• The above designs for new stationery for the new business including:
• Business Cards, Letter head, Thank-you cards, Birthday cards, Presentation folders, With Compliment slips and a powerpoint template. We also would like to send a card to all customers with the something along of the lines of "something new".
Nice to have
• It is a new look - long time family business being passed to next generation - big focus on advice for YOU, individual advice etc..

```html
<!DOCTYPE html>
<html lang="en">
<head>
<meta charset="utf-8">
<title>Tellmora Letterhead</title>
<link href="https://fonts.googleapis.com/css2?family=Montserrat:wght@400;600&family=Roboto+Condensed:wght@400&display=swap" rel="stylesheet">
<style>
  :root{
    --backdrop:#bfe6ea;
    --paper:#ffffff;
    --brand:#17b8d8;
    --brand-deep:#2a9fc0;
    --brand-light:#43bed8;
    --grey:#8a8d90;
    --grey-light:#d9dbdd;
  }
  html,body{margin:0;padding:0;width:1200px;height:784px;overflow:hidden;background:var(--backdrop);}
  .canvas{position:relative;width:1200px;height:784px;}
  .letterhead{
    position:absolute;left:338px;top:22px;width:523px;height:740px;
    background:var(--paper);box-shadow:0 6px 18px rgba(40,110,125,.25);overflow:hidden;
  }
  .edge-tab{position:absolute;width:4px;height:40px;}
  .edge-tab--left{left:0;}
  .edge-tab--right{right:0;}
  .edge-tab--blue{top:0;background:var(--brand);}
  .edge-tab--grey{top:40px;background:var(--grey);}
  .tagline{
    position:absolute;left:0;right:0;top:44px;margin:0;text-align:center;
    font-family:"Montserrat",sans-serif;font-size:7.4px;letter-spacing:.9px;text-transform:uppercase;
    color:var(--grey);white-space:nowrap;
  }
  .tagline__headline{color:var(--brand-light);}
  .brand{
    position:absolute;right:34px;top:74px;display:flex;align-items:center;gap:10px;
  }
  .brand__dot{width:22px;height:22px;border-radius:50%;background:var(--grey);}
  .brand__name{
    font-family:"Montserrat",sans-serif;font-weight:600;font-size:21px;letter-spacing:1.5px;
    text-transform:uppercase;color:var(--brand-light);
  }
  .footer-wave{position:absolute;left:0;bottom:0;width:523px;height:740px;}
  .contact{
    position:absolute;left:10px;bottom:8px;display:flex;align-items:center;gap:6px;
    font-family:"Roboto Condensed",sans-serif;font-size:9.2px;color:#fff;white-space:nowrap;
  }
  .contact__icon{width:9px;height:9px;flex:none;}
</style>
</head>
<body>
<div class="canvas">
  <article class="letterhead">
    <span class="edge-tab edge-tab--left edge-tab--blue"></span>
    <span class="edge-tab edge-tab--left edge-tab--grey"></span>
    <span class="edge-tab edge-tab--right edge-tab--blue"></span>
    <span class="edge-tab edge-tab--right edge-tab--grey"></span>

    <p class="tagline"><span class="tagline__headline">Cover built around you</span> · Personal guidance for the people and plans that matter most to you</p>

    <div class="brand">
      <span class="brand__dot"></span>
      <span class="brand__name">Tellmora</span>
    </div>

    <svg class="footer-wave" viewBox="0 0 523 740" aria-hidden="true">
      <path d="M0,566 C40,560 55,592 108,620 C228,680 432,640 500,668 C516,676 523,684 523,672 L523,740 L0,740 Z" fill="var(--grey-light)"/>
      <path d="M0,578 C45,570 55,605 110,632 C230,690 430,652 500,682 C515,690 523,696 523,688 L523,740 L0,740 Z" fill="var(--brand-deep)"/>
      <path d="M0,596 C45,590 60,618 115,642 C235,696 430,666 500,696 C515,703 523,708 523,702 L523,740 L0,740 Z" fill="var(--brand)"/>
    </svg>

    <div class="contact">
      <svg class="contact__icon" viewBox="0 0 10 10"><circle cx="5" cy="5" r="4.5" fill="none" stroke="#fff"/><path d="M5 2.5a1.6 1.6 0 0 1 1.6 1.6C6.6 5.4 5 7.5 5 7.5S3.4 5.4 3.4 4.1A1.6 1.6 0 0 1 5 2.5z" fill="#fff"/></svg>
      <span>48 Larkfield Road, Suite 210 Brisbane QLD 4000</span>
      <svg class="contact__icon" viewBox="0 0 10 10"><circle cx="5" cy="5" r="4.5" fill="none" stroke="#fff"/><path d="M3.3 2.8l1 1-.5.7a3 3 0 0 0 1.7 1.7l.7-.5 1 1-.6.8C5 7.3 2.7 5 3.3 2.8z" fill="#fff"/></svg>
      <span>(07) 3555 0142</span>
      <svg class="contact__icon" viewBox="0 0 10 10"><circle cx="5" cy="5" r="4.5" fill="none" stroke="#fff"/><rect x="3" y="4" width="4" height="3" fill="#fff"/><rect x="3.6" y="2.6" width="2.8" height="1.2" fill="#fff"/></svg>
      <span>(07) 3555 0198</span>
      <svg class="contact__icon" viewBox="0 0 10 10"><circle cx="5" cy="5" r="4.5" fill="none" stroke="#fff"/><circle cx="5" cy="5" r="2.3" fill="none" stroke="#fff" stroke-width=".8"/><line x1="2.7" y1="5" x2="7.3" y2="5" stroke="#fff" stroke-width=".8"/></svg>
      <span>www.tellmorafinancialgroup.com</span>
    </div>
  </article>
</div>
</body>
</html>
```